Business Cards Design for the electrical wholesaler: clean bold dynamic :)

We need a business card design that would follow our latest brand guidelines. As an electrical wholesaler we want to bring a fresh look and feel into the industry. The design should be clean bold and dynamic. It should come alive with the renewed energy of our green colour. Our grey colour should keep things balanced and complement the notion of maturity and responsibility. We employ Lato as a corporate font however are not bound by this font and we’re open to interpretation here.

Target Market(s)

Electrical contractors

Industry/Entity Type

Business

Contact Information for Business Card

Logo
Name & Surname: Halyna Dorosh
Job Title: Director of Marketing
Email: halya.dorosh@quillmail.example
Cell phone: XXX.XXX.XXXX
Address: 20517 - 87 Ave. Edmonton, AB, Canada. T6K 4N8
Business Phone: 780.555.0184
Website: www.brovix.example

Font styles to use
Other font styles liked:
• Lato

Requirements
Must have
• Logo & website
Nice to have
• Brand elements - some of them you may find in the attached Brand Guidelines (e.g. three lines on the background signifying "W")

```html
<!DOCTYPE html>
<html lang="en">
<head>
<meta charset="utf-8">
<title>Brovix Business Card</title>
<link rel="stylesheet" href="https://fonts.googleapis.com/css2?family=Oswald:wght@500&family=Work+Sans:wght@400;500&display=swap">
<style>
  :root {
    --backdrop: #1d1d1e;
    --card-white: #ffffff;
    --brand-grey: #58595b;
    --grey-dark: #4a4b4d;
    --brand-green: #8dc63f;
    --text-grey: #4d4e50;
  }
  * { box-sizing: border-box; margin: 0; padding: 0; }
  html, body {
    width: 1200px; height: 897px; overflow: hidden;
    background: var(--backdrop);
    font-family: "Work Sans", sans-serif;
  }
  .stage { position: relative; width: 1200px; height: 897px; }
  .card {
    position: absolute; left: 303px; width: 594px; height: 338px;
    border-radius: 18px; overflow: hidden;
  }
  .card-front { top: 92px; background: var(--card-white); }
  .card-back { top: 469px; background: var(--brand-grey); }

  .wordmark {
    position: absolute; display: flex; align-items: center; gap: 12px;
    font-family: "Work Sans", sans-serif; font-weight: 500;
    letter-spacing: -1px; line-height: 1;
  }
  .wordmark-mark { display: block; border-radius: 6px; background: var(--brand-green); }
  .card-front .wordmark { left: 28px; top: 34px; font-size: 58px; color: var(--text-grey); }
  .card-front .wordmark-mark { width: 46px; height: 46px; }
  .card-back .wordmark { left: 50%; top: 140px; transform: translateX(-50%); font-size: 66px; color: #ffffff; }
  .card-back .wordmark-mark { width: 52px; height: 52px; }

  .holder { position: absolute; left: 30px; top: 244px; width: 180px; }
  .holder-name {
    font-family: "Oswald", sans-serif; font-weight: 500;
    font-size: 26px; line-height: 1; color: var(--brand-green);
    text-transform: uppercase; letter-spacing: 0.2px; white-space: nowrap;
  }
  .holder-title { margin-top: 7px; font-size: 12.5px; color: var(--text-grey); white-space: nowrap; }

  .contact-list {
    position: absolute; left: 216px; top: 243px; list-style: none;
    font-size: 12.5px; line-height: 21px; color: var(--text-grey); white-space: nowrap;
  }
  .contact-list li { display: flex; align-items: center; gap: 8px; }
  .contact-list svg { width: 10px; height: 10px; flex: none; }
  .highlight { color: var(--brand-green); }

  .address {
    position: absolute; left: 462px; top: 243px; font-style: normal;
    font-size: 12.5px; line-height: 21px; color: var(--text-grey); white-space: nowrap;
  }

  .stripe-grey { position: absolute; left: 0; right: 0; top: 320px; height: 4px; background: var(--grey-dark); }
  .stripe-green { position: absolute; left: 0; right: 0; top: 324px; height: 14px; background: var(--brand-green); }

  .back-url {
    position: absolute; left: 0; right: 0; top: 297px; text-align: center;
    font-size: 14px; color: #ffffff; letter-spacing: 0.6px;
  }
</style>
</head>
<body>
<main class="stage">
  <section class="card card-front">
    <div class="wordmark"><span class="wordmark-mark"></span>brovix</div>

    <div class="holder">
      <p class="holder-name">Halyna Dorosh</p>
      <p class="holder-title">Director of Marketing</p>
    </div>

    <ul class="contact-list">
      <li>
        <svg viewBox="0 0 12 12" aria-hidden="true"><path d="M3 1 L5 3.5 L4 5 Q5 7 7 8 L8.5 7 L11 9 L9.5 11 Q4 10.5 1 2.5 Z" fill="var(--brand-green)"/></svg>
        780.555.0184
      </li>
      <li>
        <svg viewBox="0 0 12 12" aria-hidden="true"><rect x="1" y="2.5" width="10" height="7" fill="none" stroke="var(--brand-green)" stroke-width="1.3"/><path d="M1 3 L6 7 L11 3" fill="none" stroke="var(--brand-green)" stroke-width="1.3"/></svg>
        halya.dorosh@quillmail.example
      </li>
      <li>
        <svg viewBox="0 0 12 12" aria-hidden="true"><circle cx="6" cy="6" r="4.8" fill="none" stroke="var(--brand-green)" stroke-width="1.1"/><ellipse cx="6" cy="6" rx="2" ry="4.8" fill="none" stroke="var(--brand-green)" stroke-width="1"/><path d="M1.2 6 H10.8" stroke="var(--brand-green)" stroke-width="1"/></svg>
        <span>www.<span class="highlight">brovix</span>.example</span>
      </li>
    </ul>

    <address class="address">
      20517 87ave<br>
      T6K4N8 Edmonton,<br>
      Alberta
    </address>

    <div class="stripe-grey"></div>
    <div class="stripe-green"></div>
  </section>

  <section class="card card-back">
    <div class="wordmark"><span class="wordmark-mark"></span>brovix</div>
    <p class="back-url">www.<span class="highlight">brovix</span>.example</p>
  </section>
</main>
</body>
</html>
```